Website redesign for AI startup

Overview
We are looking to have our website https://www.hellomarlo.ai/ redesigned to look much more sophisticated and modern. We would like the brand colors to be different and less or no use of the Marlo bird character. We have included some example sites below for designs that we like. Please do not to use the same purple or purple at all on the site as we would like different brand colors and 'too much purple' has been the main comment.

Example sites that we like:
https://www.quorvant.com/
https://pagemorrow.com/
https://www.steadycloudly.com/

Requirements
Redesign the following pages from our website, modeling an example site that we like:
-Home page: https://hellomarlo.ai
-See an example: https://www.hellomarlo.ai/example-page
-Pricing: https://www.hellomarlo.ai/pricing
-Product: https://www.hellomarlo.ai/how-it-works
-Portal home: https://www.hellomarlo.ai/overview (you will need to create an account to view this; the account is free)
New design should be sleek, professional, and modern
The pages should contain the same content that it currently does.
Images on the pages should change to match the new designs and style.
Use different brand colors, these should look professional
The Marlo bird character can be used, but it’s not required. If the bird is used, it should be rarely used and not front-and-center.
Provide both desktop and mobile designs

Target Market(s)

Small business owners

Industry/Entity Type

SaaS tool

Number of Pages Required

5+ page

Requirements
Must have
• modern and sleek design, different brand colors, mobile and web designs

```html
<!DOCTYPE html>
<html lang="en">
<head>
<meta charset="utf-8">
<title>Marlo AI – Your 24/7 AI Sales Assistant</title>
<link rel="stylesheet" href="https://fonts.googleapis.com/css2?family=Montserrat:wght@400;500;600;700;800&display=swap">
<style>
:root{
  --blue:#5b9cf0;
  --blue-title:#5a9cf0;
  --ink:#1b1b1b;
  --text:#2b2b2b;
  --grey-bg:#f3f3f3;
  --white:#ffffff;
}
*{box-sizing:border-box;margin:0;padding:0}
html,body{width:1200px;height:5300px;overflow:hidden}
body{font-family:"Montserrat",sans-serif;color:var(--text);background:var(--white)}
.canvas{position:relative;width:1200px;height:5300px;overflow:hidden}
.abs{position:absolute}
.btn{display:inline-flex;align-items:center;justify-content:center;white-space:nowrap;font-family:"Montserrat",sans-serif;font-weight:700;font-size:12px;letter-spacing:.5px;text-transform:uppercase;border-radius:3px;height:44px;padding:0 22px}
.btn-dark{background:var(--ink);color:var(--white)}
.btn-white{background:var(--white);color:var(--blue)}
.btn-blue{background:var(--blue);color:var(--white)}
.photo{position:absolute}
h2.title{font-weight:700;font-size:37px;line-height:1.4;color:var(--ink)}
h2.title.blue{color:var(--blue-title)}
p.body{font-size:21px;line-height:1.45;color:var(--text)}

/* top bar */
.topbar{top:0;left:0;width:1200px;height:62px;background:var(--blue);color:var(--white);font-size:14px}
.topbar .item{position:absolute;top:12px;display:flex;align-items:center;gap:14px;white-space:nowrap}
.topbar .ico{width:38px;height:38px;border-radius:50%;background:rgba(255,255,255,.35);display:flex;align-items:center;justify-content:center}
.topbar .login{position:absolute;left:838px;top:13px;width:110px;height:36px;background:var(--white);color:var(--blue);font-size:12px;font-weight:700;display:flex;align-items:center;justify-content:center;border-radius:2px}
.topbar .register{position:absolute;left:975px;top:13px;width:112px;height:36px;background:var(--ink);color:var(--white);font-size:12px;font-weight:700;display:flex;align-items:center;justify-content:center;border-radius:2px}

/* nav */
.nav{top:62px;left:0;width:1200px;height:82px;background:var(--white);font-size:14px;font-weight:500;color:var(--ink)}
.nav a{position:absolute;top:30px;color:inherit;text-decoration:none;white-space:nowrap}
.wordmark{position:absolute;display:flex;align-items:center;gap:12px;font-weight:600;letter-spacing:3px;text-transform:uppercase;white-space:nowrap;color:var(--ink)}
.wordmark i{display:inline-block;width:16px;height:16px;border-radius:50%;background:var(--blue)}
.nav .wordmark{left:490px;top:24px;font-size:30px}

/* hero */
.hero{top:144px;left:0;width:1200px;height:583px;background:linear-gradient(90deg,#5e9cf0 0%,#79adf3 55%,#b9d4f8 100%)}
.hero h1{position:absolute;left:110px;top:126px;font-size:64px;font-weight:800;line-height:1.18;color:var(--white)}
.hero .lead{position:absolute;left:110px;top:294px;font-size:22px;line-height:1.4;color:var(--white)}
.hero .lead b{font-weight:700}
.hero .lead .dark{color:var(--ink);font-weight:700;font-size:26px}

/* engagement */
.engage{top:727px;left:0;width:1200px;height:438px;text-align:center}
.icon-row{position:absolute;top:312px;left:470px;display:flex;gap:22px}
.icon-row span{width:50px;height:50px;border-radius:50%;background:var(--blue);display:flex;align-items:center;justify-content:center}
.icon-row span.dark{background:var(--ink)}

.split{left:0;width:1200px}
.arc-tr{border-top-right-radius:150px}
.arc-tl{border-top-left-radius:150px}

/* video */
.video-box{left:107px;top:1675px;width:984px;height:589px;border:5px solid var(--ink);border-radius:18px;background:linear-gradient(90deg,#ffffff 0%,#eaf2fd 40%,#6fa6f1 100%)}
.social-dots{position:absolute;left:38px;top:180px;display:flex;flex-direction:column;gap:14px}
.social-dots span{width:30px;height:30px;border-radius:50%;background:var(--ink)}
.social-dots span.first{background:var(--blue)}

/* reviews */
.reviews{top:3287px;left:0;width:1200px;height:609px;background:linear-gradient(180deg,#f7f8fa,#ffffff)}
.review-card{position:absolute;left:198px;top:185px;width:843px;height:288px;background:var(--white);border-radius:16px;box-shadow:0 6px 30px rgba(0,0,0,.06);overflow:hidden}
.arrows{position:absolute;top:497px;display:flex;gap:18px;left:860px}
.arrows span{width:46px;height:30px;border-radius:3px;display:flex;align-items:center;justify-content:center}

/* footer */
.footer{top:4919px;left:0;width:1200px;height:381px;background:var(--blue);color:var(--white)}
.footer h4{position:absolute;top:66px;font-size:26px;font-weight:700;letter-spacing:.5px;white-space:nowrap}
.footer ul{position:absolute;top:112px;list-style:none;font-size:18px;line-height:26px;white-space:nowrap}
.footer .social li{display:flex;align-items:center;gap:14px;line-height:45px}
.footer .social i{width:28px;height:28px;border-radius:50%;background:var(--ink);display:inline-block}
.footer .wordmark{left:108px;top:66px;font-size:30px}
.chat{position:absolute;left:1007px;top:4878px;width:72px;height:72px;border-radius:50%;background:var(--ink);border:4px solid var(--blue);display:flex;align-items:center;justify-content:center}
</style>
</head>
<body>
<div class="canvas">

  <div class="abs topbar">
    <div class="item" style="left:110px">
      <span class="ico"><svg width="18" height="18" viewBox="0 0 24 24"><path d="M12 2a7 7 0 0 0-7 7c0 5 7 13 7 13s7-8 7-13a7 7 0 0 0-7-7zm0 9.5A2.5 2.5 0 1 1 12 6.5a2.5 2.5 0 0 1 0 5z" fill="#fff"/></svg></span>United States,USA
    </div>
    <div class="item" style="left:356px">
      <span class="ico"><svg width="18" height="18" viewBox="0 0 24 24"><path d="M6.6 10.8a15 15 0 0 0 6.6 6.6l2.2-2.2a1 1 0 0 1 1-.25 11.4 11.4 0 0 0 3.6.57 1 1 0 0 1 1 1V20a1 1 0 0 1-1 1A17 17 0 0 1 3 4a1 1 0 0 1 1-1h3.5a1 1 0 0 1 1 1c0 1.25.2 2.45.57 3.57a1 1 0 0 1-.25 1z" fill="#fff"/></svg></span>+1 (555) 014 2290
    </div>
    <div class="item" style="left:593px">
      <span class="ico"><svg width="18" height="18" viewBox="0 0 24 24"><rect x="3" y="5" width="18" height="14" rx="2" fill="#fff"/><path d="M3 7l9 6 9-6" stroke="#5b9cf0" stroke-width="1.6" fill="none"/></svg></span>admin@hellomarlo.ai
    </div>
    <div class="login">LOGIN</div>
    <div class="register">REGISTER</div>
  </div>

  <nav class="abs nav">
    <a style="left:110px">Home</a>
    <a style="left:190px">About</a>
    <a style="left:268px">Product</a>
    <a style="left:359px">Support</a>
    <span class="wordmark"><i></i>Marlo AI</span>
    <a style="left:802px">Pricing</a>
    <a style="left:896px">FAQ</a>
    <a style="left:964px">Referral Program</a>
  </nav>

  <section class="abs hero">
    <h1>WELCOME TO<br>MARLO AI</h1>
    <p class="lead">Save time and get more customerswith<br>Marlo AI: Your <span class="dark">24/7</span> AI <b>Sales Assistant.</b></p>
    <span class="btn btn-white abs" style="left:110px;top:392px">SEE AN EXAMPLE</span>
    <span class="btn btn-dark abs" style="left:298px;top:392px">CREATE YOUR MARLO</span>
    <div class="photo" role="img" aria-label="Smiling support agent wearing a headset" style="left:790px;top:46px;width:410px;height:537px;background:linear-gradient(180deg,#d6e4f7 0%,#eef2f8 60%,#f4f4f4 100%);border-top-left-radius:200px 240px"></div>
  </section>

  <section class="abs engage">
    <h2 class="title" style="position:absolute;top:73px;width:100%">24/7 CUSTOMER ENGAGEMENT</h2>
    <p class="body" style="position:absolute;top:140px;left:220px;width:760px">Marlo interacts with your leads across email, chatbot, phone, and text around the clock</p>
    <span class="btn btn-dark abs" style="left:494px;top:222px;width:212px;padding:0 10px">SEE AN EXAMPLE HERE.</span>
    <div class="icon-row">
      <span><svg width="24" height="24" viewBox="0 0 24 24"><path d="M4 4h16v12H8l-4 4z" fill="#fff"/><circle cx="9" cy="10" r="1.2" fill="#5b9cf0"/><circle cx="12" cy="10" r="1.2" fill="#5b9cf0"/><circle cx="15" cy="10" r="1.2" fill="#5b9cf0"/></svg></span>
      <span class="dark"><svg width="24" height="24" viewBox="0 0 24 24"><circle cx="12" cy="12" r="10" fill="#fff"/><path d="M8.5 10a7 7 0 0 0 5.5 5.5l1.3-1.3 2 1-.8 2.3A9 9 0 0 1 7 8.3l2.3-.8 1 2z" fill="#1b1b1b"/></svg></span>
      <span><svg width="24" height="24" viewBox="0 0 24 24"><rect x="3" y="6" width="18" height="12" rx="2" fill="#fff"/><path d="M3 7l9 6 9-6" stroke="#5b9cf0" stroke-width="1.6" fill="none"/></svg></span>
      <span><svg width="24" height="24" viewBox="0 0 24 24"><rect x="8" y="3" width="11" height="14" rx="2" fill="#fff"/><rect x="5" y="7" width="11" height="14" rx="2" fill="#fff" stroke="#5b9cf0" stroke-width="1.5"/></svg></span>
    </div>
  </section>

  <section class="abs split" style="top:1165px;height:422px;background:var(--grey-bg)">
    <div class="photo arc-tr" role="img" aria-label="Team of colleagues planning around a table with sticky notes" style="left:0;top:0;width:486px;height:422px;background:linear-gradient(135deg,#cfd8e3,#9aa9bb 60%,#6f7a88)"></div>
    <h2 class="title abs" style="left:598px;top:62px">LEAD QUALIFICATION &amp;<br>PRIORITIZATION</h2>
    <p class="body abs" style="left:598px;top:176px;width:450px">Marlo captures, engages, and qualifies leads, helping you focus onthe most promisingopportunities.</p>
    <span class="btn btn-dark abs" style="left:600px;top:304px">CLICK HEREE</span>
  </section>

  <section class="abs video-box">
    <h2 class="title" style="position:absolute;top:30px;width:100%;text-align:center">WHAT IS MARLO AI?</h2>
    <div class="social-dots"><span class="first"></span><span></span><span></span><span></span><span></span></div>
    <div class="photo" role="img" aria-label="Video still of a man with a headset working at a computer" style="left:96px;top:119px;width:784px;height:333px;border-radius:12px;background:linear-gradient(90deg,#2d3440,#5e6b7c 45%,#8d9bad)"></div>
    <svg class="abs" style="left:463px;top:261px" width="50" height="50" viewBox="0 0 50 50"><circle cx="25" cy="25" r="23" fill="#fff" stroke="#1b1b1b" stroke-width="2"/><path d="M20 16l14 9-14 9z" fill="#1b1b1b"/></svg>
    <span class="btn btn-dark abs" style="left:405px;top:495px;width:168px;height:46px">WATCH VIDEO</span>
  </section>

  <section class="abs split" style="top:2352px;height:509px">
    <h2 class="title blue abs" style="left:112px;top:74px">AUTOMATED SCHEDULING</h2>
    <p class="body abs" style="left:112px;top:142px;width:400px">Marlo books meetings with qualified leads directly on your calendar, streamlining your sales process.</p>
    <span class="btn btn-blue abs" style="left:112px;top:300px;width:151px">CLICK HERE</span>
    <div class="photo arc-tl" role="img" aria-label="Hand touching a digital calendar display" style="left:712px;top:0;width:488px;height:424px;background:linear-gradient(135deg,#a7c2df,#6f93bb 60%,#3f5c80)"></div>
  </section>

  <section class="abs split" style="top:2861px;height:426px;background:var(--blue)">
    <div class="photo arc-tr" role="img" aria-label="Businesswoman on the phone at her desk" style="left:0;top:0;width:486px;height:426px;background:linear-gradient(135deg,#f2efe9,#ddd6cd 60%,#bdb4a9)"></div>
    <h2 class="title abs" style="left:598px;top:72px;color:var(--white)">CUSTOMIZE YOUR<br>ASSISTANT</h2>
    <p class="body abs" style="left:598px;top:185px;width:500px;color:var(--white)">Change your phone number, email, how Marlo engages with your leads, and much more, turning every interaction into an opportunity.</p>
    <span class="btn btn-white abs" style="left:600px;top:305px;width:152px;height:42px">CLICK HEREE</span>
  </section>

  <section class="abs reviews">
    <h2 class="title blue" style="position:absolute;top:76px;width:100%;text-align:center">CLIENT REVIEWS</h2>
    <div class="review-card">
      <svg class="abs" style="left:18px;top:16px" width="46" height="40" viewBox="0 0 46 40"><path d="M4 36V22C4 10 10 4 20 2l2 5c-6 2-9 6-9 11h8v18zM26 36V22c0-12 6-18 16-20l2 5c-6 2-9 6-9 11h8v18z" fill="#5b9cf0"/></svg>
      <p class="abs" style="left:64px;top:62px;width:460px;font-size:14px;line-height:26px;color:#333">"We've been exploring chatbots to help convert website visitors to leads and Marlo AI was 10x better than any other option we explored."</p>
      <p class="abs" style="left:64px;top:148px;font-size:26px;font-weight:700;color:var(--blue-title)">Dana Whitfield</p>
      <p class="abs" style="left:64px;top:200px;font-size:17px;color:#333">VP of Business Dev.</p>
      <div class="photo" role="img" aria-label="Portrait of a smiling businessman in a blue suit" style="left:586px;top:0;width:257px;height:288px;background:linear-gradient(180deg,#2f4d7a,#1f3660)"></div>
    </div>
    <div class="arrows">
      <span style="background:#f0d9c4"><svg width="26" height="12" viewBox="0 0 26 12"><path d="M25 6H2M7 1L2 6l5 5" stroke="#1b1b1b" stroke-width="1.6" fill="none"/></svg></span>
      <span style="background:var(--blue)"><svg width="26" height="12" viewBox="0 0 26 12"><path d="M1 6h23M19 1l5 5-5 5" stroke="#1b1b1b" stroke-width="1.6" fill="none"/></svg></span>
    </div>
  </section>

  <section class="abs split" style="top:3896px;height:426px;background:var(--grey-bg)">
    <h2 class="title abs" style="left:105px;top:84px">RAPID AND EFFECTIVE<br>AI TRAINING</h2>
    <p class="body abs" style="left:105px;top:196px;width:420px">Marlo analyzes your website, allowing Marlo to provide accurate and up-to-date information to your leads.</p>
    <span class="btn btn-dark abs" style="left:107px;top:318px;width:151px">CLICK HEREE</span>
    <div class="photo arc-tl" role="img" aria-label="Smiling man talking on a desk phone in a bright office" style="left:712px;top:0;width:488px;height:426px;background:linear-gradient(135deg,#e6edf5,#c3d1e1 60%,#9fb2c8)"></div>
  </section>

  <section class="abs split" style="top:4322px;height:597px">
    <div class="photo arc-tr" role="img" aria-label="Two colleagues reviewing a tablet together" style="left:0;top:82px;width:486px;height:422px;background:linear-gradient(135deg,#8a8a8a,#5a5652 60%,#3a3633)"></div>
    <h2 class="title blue abs" style="left:625px;top:126px">SEAMLESS TOOL<br>INTEGRATION</h2>
    <p class="body abs" style="left:625px;top:236px;width:480px">Marlo AI's streamlined tool integrations effortlessly sync with your existing business tools and platforms, ensuring a smooth and seamless setup.</p>
    <span class="btn btn-dark abs" style="left:627px;top:390px;width:151px">CLICK HEREE</span>
  </section>

  <footer class="abs footer">
    <span class="wordmark"><i style="background:var(--ink)"></i>Marlo AI</span>
    <p class="abs" style="left:110px;top:146px;font-size:24px;font-weight:700;line-height:34px;white-space:nowrap">SET UP<br>YOUR OWN MARLO</p>
    <span class="btn btn-dark abs" style="left:110px;top:236px;width:172px;height:46px;padding:0 10px">CREATE YOUR MARLO</span>
    <h4 style="left:405px">ABOUT INFO</h4>
    <ul style="left:405px"><li>Home</li><li>Product</li><li>Support</li><li>Pricing</li><li>FAQ</li><li>Referral Program</li></ul>
    <h4 style="left:667px">QUICK LINKS</h4>
    <ul style="left:667px"><li>Let us know!</li><li>Privacy Policy</li><li>Terms of Use</li><li>Careers</li><li>Site map</li><li>Contact us</li></ul>
    <h4 style="left:928px">FOLLOW US</h4>
    <ul class="social" style="left:930px;top:106px"><li><i></i>Friendwall.</li><li><i></i>Worknet.</li><li><i></i>Clipstream.</li><li><i></i>Snapfolio.</li></ul>
    <p class="abs" style="left:0;width:100%;text-align:center;top:336px;font-size:18px">© 2024 HelloMarlo.ai. All rights reserved.</p>
  </footer>
  <div class="chat"><svg width="32" height="32" viewBox="0 0 32 32"><path d="M16 5C9.4 5 4 9.7 4 15.5c0 2.6 1.1 5 2.9 6.8L6 27l5-2.2c1.5.5 3.2.8 5 .8 6.6 0 12-4.7 12-10.5S22.6 5 16 5z" fill="none" stroke="#fff" stroke-width="2"/><circle cx="11" cy="15.5" r="1.5" fill="#fff"/><circle cx="16" cy="15.5" r="1.5" fill="#fff"/><circle cx="21" cy="15.5" r="1.5" fill="#fff"/></svg></div>

</div>
</body>
</html>
```